8'x8' Exhibit Backdrop for Healthcare Events focused on the 55 and older crowds

8X8 Backdrop for Exhibiting.

I also want a design for a 6' table skirt to include our logo on two sides and the logo with Hereditary Cancer Screening underneath on the front. I want the main message of Will You Give your Loved Ones The Information To Beat Cancer in Their Lives to be completely centered on the 8X8 backdrop. Hereditary Cancer Screening The Test You Take For Them in the top left corner and the purple box on the right hand side - just like the photo that has been uploaded below. I need High resolution photos around the backdrop but not so large that they overtake the main message.

Target Market(s)

55+ crowd living in Adult only communities. They have an active lifestyle

Industry/Entity Type

Healthcare

Other font styles liked:
• "The Test You Take For Them" is Comic Sans

Colors
0255a3
fbed22
ffffff

Requirements
Must have
• I am posting a photo of the exact backdrop I would like to see. There are red arrows showing where to move certain items. There is a space underneath the slogan WILL YOU GIVE YOUR LOVED ONES... where another photo will go. Add another photo underneath the slogan that you are moving up - GIVE THEM THE GIFT OF KNOWLEDGE
• See the upload section for the new photo
• Do this one exactly like I am asking for and then you can show me some of your ideas. Thanks
• THE PHOTOS UPLOADED ARE EXAMPLES. FEEL FREE TO SEARCH OUT YOUR OWN HIGH RESOLUTION PHOTOS. THANKS

```html
<!DOCTYPE html>
<html lang="en">
<head>
<meta charset="utf-8">
<title>Hereditary Cancer Screening Backdrop</title>
<link rel="stylesheet" href="https://fonts.googleapis.com/css2?family=Montserrat:wght@400;600;700;800&family=Oswald:wght@300;400;500;700&display=swap">
<style>
  :root {
    --navy: #0f1f5e;
    --green: #8cc63f;
    --white: #ffffff;
    --stage: #e4e4e4;
    --warm-a: #c99a78;
    --warm-b: #6f8a4e;
    --cool-a: #9aa6b8;
    --cool-b: #d8c6b2;
  }
  * { box-sizing: border-box; margin: 0; padding: 0; }
  html, body { width: 1200px; height: 1200px; overflow: hidden; }
  body { background: var(--stage); position: relative; font-family: "Montserrat", sans-serif; }

  .backdrop {
    position: absolute; left: 20px; top: 130px; width: 1160px; height: 940px;
    background: var(--white); overflow: hidden;
  }
  .backdrop > * { position: absolute; }

  .photo { background: linear-gradient(135deg, var(--warm-a), var(--warm-b)); }
  .photo.soft { background: linear-gradient(160deg, var(--cool-b), var(--warm-a)); }
  .photo.indoor { background: linear-gradient(120deg, var(--cool-b), var(--cool-a)); }
  .photo.garden { background: linear-gradient(140deg, #b98d6e, #587a3c); }

  .title { left: 46px; top: 64px; width: 330px; text-align: right; color: var(--navy); line-height: 1; }
  .title .t-bold { font-weight: 800; font-size: 48px; letter-spacing: 1px; display: block; }
  .title .t-light { font-weight: 400; font-size: 45px; letter-spacing: 1px; display: block; margin-top: 2px; }
  .tagline {
    left: 46px; top: 222px; width: 328px; height: 25px; background: var(--green);
    color: var(--white); font-weight: 600; font-size: 18px; line-height: 25px; text-align: center;
  }

  .rule { background: var(--navy); }

  .brand { left: 62px; top: 858px; display: flex; align-items: center; gap: 12px; }
  .brand-mark { width: 22px; height: 22px; background: var(--green); }
  .brand-name {
    color: var(--navy); font-weight: 700; font-size: 30px; line-height: 1; letter-spacing: 2px; white-space: nowrap;
  }

  .headline { left: 406px; top: 396px; width: 350px; color: var(--navy); font-family: "Oswald", sans-serif; font-weight: 300; line-height: 1; }
  .headline .line { display: block; font-size: 51px; white-space: nowrap; letter-spacing: -0.5px; }
  .headline .line + .line { margin-top: 6px; font-size: 47px; }
  .headline strong { font-weight: 700; margin-left: 14px; }

  .info-bar {
    left: 406px; top: 518px; width: 347px; height: 43px; background: var(--navy);
    color: var(--white); font-weight: 700; font-size: 21px; line-height: 43px; text-align: center; letter-spacing: 0.5px;
  }
  .cancer-word {
    left: 420px; top: 562px; color: var(--green); font-family: "Oswald", sans-serif; font-weight: 500;
    font-size: 70px; line-height: 1; letter-spacing: 9px;
  }
  .cancer-tail {
    left: 427px; top: 636px; color: var(--navy); font-family: "Oswald", sans-serif; font-weight: 400;
    font-size: 33px; line-height: 1; letter-spacing: -0.5px;
  }

  .knowledge-panel { left: 774px; top: 50px; width: 340px; height: 532px; background: var(--navy); }
  .knowledge-photo {
    position: absolute; left: 0; top: 0; width: 100%; height: 380px;
    background: linear-gradient(180deg, #8a7a8c 0%, #5b5f8a 55%, var(--navy) 100%);
  }
  .knowledge-copy { position: absolute; right: 12px; top: 360px; text-align: right; color: var(--white); }
  .knowledge-copy .k-big { font-family: "Oswald", sans-serif; font-size: 40px; line-height: 1; }
  .knowledge-copy .k-big b { font-weight: 700; }
  .knowledge-copy .k-big span { font-weight: 300; }
  .knowledge-copy .k-mid { font-size: 17px; font-weight: 400; letter-spacing: 0.5px; margin-top: 4px; }
  .knowledge-copy .k-huge { font-family: "Oswald", sans-serif; font-weight: 700; font-size: 42px; line-height: 1; margin-top: 8px; }
  .knowledge-copy .k-small { font-size: 12.5px; margin-top: 6px; line-height: 16px; }
  .knowledge-copy .k-small b { font-weight: 700; }

  .web { left: 776px; top: 880px; width: 339px; text-align: center; color: var(--navy); font-weight: 600; font-size: 13px; letter-spacing: 1.5px; }
</style>
</head>
<body>
  <section class="backdrop">
    <div class="title">
      <span class="t-bold">Hereditary</span>
      <span class="t-light">Cancer</span>
      <span class="t-light">Screening</span>
    </div>
    <div class="tagline">The Test You Take For Them</div>

    <div class="photo" style="left:0;top:274px;width:393px;height:251px" role="img" aria-label="Laughing grandmother kissed on both cheeks by her grandchildren"></div>
    <div class="photo indoor" style="left:0;top:537px;width:394px;height:245px" role="img" aria-label="Grandparents sitting with two smiling grandchildren at home"></div>

    <div class="rule" style="left:0;top:813px;width:410px;height:9px"></div>
    <div class="brand">
      <div class="brand-mark"></div>
      <div class="brand-name">KINWELL CARE</div>
    </div>

    <div class="photo garden" style="left:406px;top:43px;width:340px;height:202px" role="img" aria-label="Three generations of women hugging and smiling"></div>
    <div class="photo soft" style="left:406px;top:257px;width:166px;height:134px" role="img" aria-label="Grandfather hugging a young grandson"></div>
    <div class="photo indoor" style="left:580px;top:257px;width:166px;height:134px" role="img" aria-label="Large family gathered in a kitchen"></div>

    <div class="headline">
      <span class="line">WILL YOU<strong>GIVE</strong></span>
      <span class="line">YOUR LOVED ONES</span>
    </div>
    <div class="info-bar">the information to Beat</div>
    <div class="rule" style="left:406px;top:561px;width:12px;height:379px"></div>
    <div class="cancer-word">CANCER</div>
    <div class="cancer-tail">IN THEIR LIVES?</div>

    <div class="photo garden" style="left:425px;top:685px;width:157px;height:125px" role="img" aria-label="Grandfather and grandson looking at something together outdoors"></div>
    <div class="photo" style="left:589px;top:685px;width:158px;height:125px" role="img" aria-label="Family relaxing together on the grass"></div>
    <div class="rule" style="left:418px;top:817px;width:331px;height:9px"></div>
    <div class="photo soft" style="left:427px;top:833px;width:312px;height:101px" role="img" aria-label="Family reading together with grandparents and children"></div>

    <div class="knowledge-panel">
      <div class="knowledge-photo" role="img" aria-label="Grandmother and granddaughter embracing cheek to cheek"></div>
      <div class="knowledge-copy">
        <div class="k-big"><b>GIVE</b> <span>THEM</span></div>
        <div class="k-mid">THE GIFT OF</div>
        <div class="k-huge">KNOWLEDGE</div>
        <div class="k-small">knowing is better than not knowing.<br><b>Knowledge is Power</b></div>
      </div>
    </div>

    <div class="photo indoor" style="left:776px;top:593px;width:166px;height:133px" role="img" aria-label="Grandfather with granddaughter hugging him"></div>
    <div class="photo soft" style="left:949px;top:593px;width:166px;height:133px" role="img" aria-label="Grandmother hugged from behind by granddaughter"></div>
    <div class="photo garden" style="left:776px;top:735px;width:166px;height:132px" role="img" aria-label="Grandparents and grandchild smiling outdoors"></div>
    <div class="photo" style="left:949px;top:735px;width:166px;height:132px" role="img" aria-label="Grandparents sitting with young grandchildren"></div>

    <div class="web">www.kinfolkscreening.com</div>
  </section>
</body>
</html>
```